KRL Stationery Design Project

Dear Designers,
We need a new stationery design for company to match our new logo.
Designers should provide a design for the following:
1. Business Card: 3.5x2 Inches.
2. Letterhead: A4 size.
3. Envelops: 25x35.5 Cm.
You can keep the Arabic name at the bottom of the logo Or you can use the separate attached Arabic Name.
Please refer to the attached logo guide for design information.
Sample Business Card information:
Name: Tarek Sowan
Position: Operation Manager
Tel: +966 920007164 Ex. 500
Fax: +966 (3)8842617
Mob: +966 (5)00263817
email: tarek@krl-example.com.sa
URL: www.krl-example.com.sa
Address:
Nakheel Heights, Suite 718
Zayed bin Omar Str.
Khobar, 31847
Saudi Arabia
Updates
Dear All,
Please note, we had uploaded our logo along with Arabic writing in Adobe illustrator format (.ai).
Regards,
Karim
Dear All,
A sample data for the business card had been added as per your request.
Regards,
Karim

```html
<!DOCTYPE html>
<html lang="en">
<head>
<meta charset="utf-8">
<title>KRL Business Card</title>
<link rel="stylesheet" href="https://fonts.googleapis.com/css2?family=Source+Sans+3:wght@400;600;700&display=swap">
<style>
  :root {
    --backdrop: #1c1c1c;
    --navy: #0d2c52;
    --navy-deep: #0a2545;
    --white: #ffffff;
    --rule-grey: #9a9ca0;
    --text-light: #e8edf3;
  }
  * { margin: 0; padding: 0; box-sizing: border-box; }
  html, body {
    width: 1200px;
    height: 472px;
    overflow: hidden;
    background: var(--backdrop);
    font-family: "Source Sans 3", Arial, sans-serif;
  }
  .canvas { position: relative; width: 1200px; height: 472px; }

  .card {
    position: absolute;
    top: 83px;
    width: 521px;
    height: 300px;
    overflow: hidden;
  }
  .card--front { left: 57px; background: var(--white); }
  .card--back { left: 610px; background: var(--navy); }

  /* Front */
  .front-brand {
    position: absolute;
    left: 0; top: 0;
    width: 100%; height: 164px;
    display: flex;
    align-items: center;
    justify-content: center;
    gap: 14px;
  }
  .brand-mark {
    width: 34px; height: 34px;
    background: var(--navy);
  }
  .brand-name {
    font-weight: 700;
    font-size: 64px;
    line-height: 1;
    letter-spacing: 2px;
    color: var(--navy);
  }
  .front-rule {
    position: absolute;
    left: 0; top: 164px;
    width: 100%; height: 5px;
    background: var(--rule-grey);
  }
  .front-band {
    position: absolute;
    left: 0; top: 169px;
    width: 100%; height: 131px;
    background: var(--navy);
    color: var(--white);
  }
  .holder {
    position: absolute;
    left: 56px; top: 24px;
    font-size: 15px;
  }
  .holder-name { font-weight: 700; font-size: 16px; }
  .holder-title { font-weight: 400; font-size: 13px; }

  .contact {
    position: absolute;
    left: 53px; top: 64px;
    display: flex;
    font-size: 12.5px;
    line-height: 17px;
    color: var(--text-light);
  }
  .contact-group { padding: 0 10px; }
  .contact-group:first-child { padding-left: 0; }
  .contact-group + .contact-group { border-left: 1px solid var(--text-light); }
  .contact-line { display: flex; align-items: center; gap: 6px; white-space: nowrap; }
  .contact-line svg { width: 11px; height: 11px; flex: none; }

  /* Back */
  .back-brand {
    position: absolute;
    left: 0; top: 100px;
    width: 100%;
    display: flex;
    align-items: center;
    justify-content: center;
    gap: 14px;
  }
  .back-brand .brand-mark { background: var(--white); }
  .back-brand .brand-name { color: var(--white); }
  .back-url {
    position: absolute;
    left: 0; top: 248px;
    width: 100%;
    text-align: center;
    font-size: 12.5px;
    letter-spacing: 2.6px;
    color: var(--white);
  }
</style>
</head>
<body>
<div class="canvas">

  <section class="card card--front">
    <div class="front-brand">
      <span class="brand-mark"></span>
      <span class="brand-name">KRL</span>
    </div>
    <div class="front-rule"></div>
    <div class="front-band">
      <p class="holder"><span class="holder-name">YOUR NAME,</span> <span class="holder-title">Title</span></p>
      <div class="contact">
        <div class="contact-group">
          <p class="contact-line">Street Name, City Name</p>
          <p class="contact-line">State, City Zip 123 4560</p>
        </div>
        <div class="contact-group">
          <p class="contact-line">
            <svg viewBox="0 0 12 12" aria-hidden="true"><circle cx="6" cy="6" r="5.3" fill="none" stroke="#fff" stroke-width="1"/><path d="M4 3.2l1 1.6-.7.7a4 4 0 0 0 2.2 2.2l.7-.7 1.6 1-.6 1C5.6 9 3 6.4 3 4z" fill="#fff"/></svg>
            123-456-7890
          </p>
          <p class="contact-line">
            <svg viewBox="0 0 12 12" aria-hidden="true"><path d="M2 6l1.3-3h5.4L10 6v3H2z" fill="#fff"/><circle cx="3.5" cy="9.5" r="1.2" fill="#fff"/><circle cx="8.5" cy="9.5" r="1.2" fill="#fff"/></svg>
            123-456-7890
          </p>
        </div>
        <div class="contact-group">
          <p class="contact-line">
            <svg viewBox="0 0 12 12" aria-hidden="true"><rect x="1" y="3" width="10" height="7" fill="#fff"/><path d="M1 3l5 4 5-4" fill="none" stroke="#0d2c52" stroke-width="1"/></svg>
            info@krl-example.com.sa
          </p>
          <p class="contact-line">
            <svg viewBox="0 0 12 12" aria-hidden="true"><circle cx="6" cy="6" r="5" fill="#fff"/><path d="M1 6h10M6 1c-2 2.5-2 7.5 0 10M6 1c2 2.5 2 7.5 0 10" fill="none" stroke="#0d2c52" stroke-width=".8"/></svg>
            www.website.com
          </p>
        </div>
      </div>
    </div>
  </section>

  <section class="card card--back">
    <div class="back-brand">
      <span class="brand-mark"></span>
      <span class="brand-name">KRL</span>
    </div>
    <p class="back-url">www.website.com</p>
  </section>

</div>
</body>
</html>
```